Heron Loan Partners Business Card

We need a business card design for our mortgage servicing company. In addition to servicing the loans of homeowners, we help homeowners with purchasing their homes and any mortgage refinancing. We would like to see designs that use the colors in the logo attached below (gold-ish yellow and navy blue), and any other design you deem fit! The design should communicate a simpler life with smart mortgages provided by Heron.

```html
<!DOCTYPE html>
<html lang="en">
<head>
<meta charset="utf-8">
<title>Heron Loan Partners – Business Card</title>
<link href="https://fonts.googleapis.com/css2?family=Montserrat:wght@400;500;700&display=swap" rel="stylesheet">
<style>
  :root {
    --navy: #25204f;
    --gold: #e2b13c;
    --white: #ffffff;
    --ink: #1c1c1c;
    --backdrop: #474747;
  }
  * { margin: 0; padding: 0; box-sizing: border-box; }
  html, body { width: 1200px; height: 1200px; overflow: hidden; }
  body {
    background: var(--backdrop);
    font-family: "Montserrat", Arial, sans-serif;
    position: relative;
  }
  .card {
    position: absolute;
    left: 193px;
    width: 818px;
    height: 464px;
    border-radius: 26px;
    overflow: hidden;
  }
  .card--front { top: 174px; background: var(--white); }
  .card--back { top: 684px; background: var(--navy); }

  .holder { position: absolute; left: 46px; top: 70px; }
  .holder__name {
    font-weight: 700; font-size: 25px; letter-spacing: -0.3px;
    color: var(--navy);
  }
  .holder__name .surname { color: var(--gold); }
  .holder__role { font-size: 20px; color: var(--ink); margin-top: 6px; }

  .brand-mark {
    position: absolute; left: 400px; top: 72px; width: 370px;
    display: flex; align-items: center; justify-content: center; gap: 12px;
    font-weight: 700; font-size: 30px; color: var(--gold); white-space: nowrap;
  }
  .brand-mark__dot { width: 16px; height: 16px; border-radius: 50%; background: var(--navy); flex: none; }

  .contacts { position: absolute; left: 44px; top: 284px; list-style: none; }
  .contacts li {
    display: flex; align-items: center; height: 32.5px;
    font-size: 20px; color: var(--ink);
  }
  .contacts svg { width: 22px; height: 22px; margin-right: 12px; fill: var(--gold); flex: none; }

  .address {
    position: absolute; left: 533px; top: 318px;
    font-size: 20px; line-height: 29px; color: var(--ink);
  }
  .bands { position: absolute; left: 0; top: 0; width: 818px; height: 464px; }

  .back-brand {
    position: absolute; inset: 0;
    display: flex; align-items: center; justify-content: center; gap: 22px;
    font-weight: 700; font-size: 60px; color: var(--gold); white-space: nowrap;
  }
  .back-brand__dot { width: 30px; height: 30px; border-radius: 50%; background: var(--white); flex: none; }
</style>
</head>
<body>

<section class="card card--front" aria-label="Business card front">
  <svg class="bands" viewBox="0 0 818 464" aria-hidden="true">
    <path d="M0,411 H553 C530,420 512,430 488,430 H0 Z" fill="var(--gold)"/>
    <path d="M0,440 H470 C520,440 545,430 572,418 C596,407 600,402 622,402 H818 V464 H0 Z" fill="var(--navy)"/>
  </svg>

  <div class="holder">
    <p class="holder__name">DANA <span class="surname">WHITFIELD</span></p>
    <p class="holder__role">Owner</p>
  </div>

  <div class="brand-mark"><span class="brand-mark__dot"></span>Heron Loan Partners</div>

  <ul class="contacts">
    <li>
      <svg viewBox="0 0 24 24"><path d="M2,9 C2,5 22,5 22,9 L22,11 L17,11 L17,8.5 L7,8.5 L7,11 L2,11 Z M6,12 H18 L20,20 H4 Z"/></svg>
      555.214.0876
    </li>
    <li>
      <svg viewBox="0 0 24 24"><path d="M2,5 H22 L12,13 Z M2,7.5 L12,15.5 L22,7.5 V19 H2 Z"/></svg>
      info@heronloanpartners.com
    </li>
    <li>
      <svg viewBox="0 0 24 24"><circle cx="12" cy="12" r="10"/><path d="M6,7 C9,8 8,11 11,12 C13,13 11,16 13,19" stroke="#fff" stroke-width="1.6" fill="none"/></svg>
      www.heronloanpartners.com
    </li>
  </ul>

  <p class="address">2400 Lakeview Blvd, Ste<br>210, Austin, TX 78701</p>
</section>

<section class="card card--back" aria-label="Business card back">
  <div class="back-brand"><span class="back-brand__dot"></span>Heron Loan Partners</div>
</section>

</body>
</html>
```